Irrigation Business needs their business cards modernised and revamped

I would like to keep my current logo, colours and revamp the format of the card.

I would like the card to be clean yet important.

Im not sure if you include texture but i would like the named logo to be indented into the card etc.

show me something alive and free something thats clinical to the point yet has a feel of achievement. i would like people to go nice card.

Target Market(s)

high end clients, corporate, sports field manger, the guys that make the decisions

Industry/Entity Type

Business

Contact Information for Business Card

nformation to be included

Dean Harlow (Director)
0487305526
dean@kolvat.biz
www.kestonfieldworks.com

instagram logo
google logo
facebook logo

Colors

Designer to choose colors to be used in the design.

Requirements
Nice to have
• indentations a really nice feel to the card good texture

```html
<!DOCTYPE html>
<html lang="en">
<head>
<meta charset="utf-8">
<title>Keston Fieldworks – Business Card</title>
<link rel="stylesheet" href="https://fonts.googleapis.com/css2?family=Open+Sans:wght@400;600;700&display=swap">
<style>
  :root {
    --stage: #2b2c2f;
    --card-white: #f4f5f5;
    --blue-deep: #2f66ad;
    --blue-mid: #3a7fc4;
    --blue-sky: #4fb0e2;
    --blue-light: #3fa9dc;
    --green: #3aa846;
    --ink: #4a4a4a;
    --white: #ffffff;
  }
  html, body {
    margin: 0;
    padding: 0;
    width: 1200px;
    height: 840px;
    overflow: hidden;
    background: var(--stage);
    font-family: "Open Sans", Arial, sans-serif;
  }
  .stage {
    position: relative;
    width: 1200px;
    height: 840px;
    display: flex;
    align-items: center;
    justify-content: center;
    gap: 40px;
  }
  .card {
    position: relative;
    width: 540px;
    height: 309px;
    overflow: hidden;
    box-shadow: 0 12px 30px rgba(0,0,0,0.45);
  }

  /* Back of card */
  .card--back {
    background: linear-gradient(100deg, var(--blue-sky) 0%, var(--blue-mid) 55%, var(--blue-deep) 100%);
    display: flex;
    flex-direction: column;
    align-items: center;
    justify-content: center;
  }
  .brand-seal {
    display: flex;
    align-items: center;
    gap: 12px;
    margin-top: -6px;
  }
  .brand-seal__dot {
    width: 22px;
    height: 22px;
    border: 3px solid var(--white);
    border-radius: 50%;
  }
  .brand-seal__name {
    color: var(--white);
    font-weight: 700;
    font-size: 26px;
    letter-spacing: 1px;
    text-transform: uppercase;
  }
  .social-row {
    position: absolute;
    bottom: 52px;
    left: 50%;
    transform: translateX(-50%);
    display: flex;
    gap: 8px;
  }
  .social-row__badge {
    width: 16px;
    height: 16px;
    border-radius: 50%;
    background: var(--white);
  }

  /* Front of card */
  .card--front {
    background: var(--card-white);
  }
  .name-disc {
    position: absolute;
    left: -30px;
    top: 40px;
    width: 330px;
    height: 330px;
    border-radius: 50%;
    background: var(--blue-deep);
  }
  .name-disc__inner {
    position: absolute;
    inset: 10px;
    border-radius: 50%;
    border: 6px solid var(--white);
    background: linear-gradient(180deg, var(--blue-light) 0%, var(--blue-mid) 70%, var(--blue-deep) 100%);
  }
  .holder {
    position: absolute;
    left: 88px;
    top: 112px;
    width: 110px;
    padding: 14px 8px;
    background: var(--white);
    border-radius: 55px 55px 55px 55px;
    text-align: center;
  }
  .holder__name {
    color: var(--blue-deep);
    font-weight: 700;
    font-size: 13px;
    line-height: 1.2;
  }
  .holder__role {
    color: var(--green);
    font-weight: 400;
    font-size: 13px;
    line-height: 1.3;
  }
  .brand-mark {
    position: absolute;
    right: 26px;
    top: 44px;
    display: flex;
    align-items: center;
    gap: 8px;
  }
  .brand-mark__dot {
    width: 26px;
    height: 26px;
    border-radius: 50%;
    background: var(--blue-light);
  }
  .brand-mark__name {
    color: var(--blue-deep);
    font-weight: 700;
    font-size: 17px;
    text-transform: uppercase;
    letter-spacing: 0.3px;
  }
  .contact-list {
    position: absolute;
    right: 24px;
    top: 150px;
    margin: 0;
    padding: 0;
    list-style: none;
    text-align: right;
  }
  .contact-list__item {
    display: flex;
    justify-content: flex-end;
    align-items: center;
    gap: 6px;
    color: var(--ink);
    font-size: 12.5px;
    line-height: 20px;
  }
  .contact-list__icon {
    width: 11px;
    height: 11px;
    flex: none;
  }
</style>
</head>
<body>
<main class="stage">

  <section class="card card--back" aria-label="Card back">
    <div class="brand-seal">
      <span class="brand-seal__dot"></span>
      <span class="brand-seal__name">Keston Fieldworks</span>
    </div>
    <div class="social-row" aria-label="Social profiles">
      <span class="social-row__badge"></span>
      <span class="social-row__badge"></span>
      <span class="social-row__badge"></span>
    </div>
  </section>

  <section class="card card--front" aria-label="Card front">
    <div class="name-disc">
      <div class="name-disc__inner"></div>
    </div>
    <div class="holder">
      <div class="holder__name">Dean Harlow</div>
      <div class="holder__role">Director</div>
    </div>

    <div class="brand-mark">
      <span class="brand-mark__dot"></span>
      <span class="brand-mark__name">Keston Fieldworks</span>
    </div>

    <ul class="contact-list">
      <li class="contact-list__item">0487305526
        <svg class="contact-list__icon" viewBox="0 0 12 12" aria-hidden="true">
          <path d="M2.5 1 L4.5 1 L5.2 3.4 L4 4.4 Q5.2 7 7.6 8 L8.6 6.8 L11 7.5 L11 9.5 Q10.5 11 9 11 Q1 10 1 3 Q1 1.5 2.5 1 Z" fill="var(--blue-deep)"/>
        </svg>
      </li>
      <li class="contact-list__item">dean@kolvat.biz
        <svg class="contact-list__icon" viewBox="0 0 12 12" aria-hidden="true">
          <rect x="0.5" y="2.5" width="11" height="7.5" rx="1" fill="var(--blue-deep)"/>
          <path d="M1 3 L6 7 L11 3" stroke="var(--white)" stroke-width="1" fill="none"/>
        </svg>
      </li>
      <li class="contact-list__item">www.kestonfieldworks.com
        <svg class="contact-list__icon" viewBox="0 0 12 12" aria-hidden="true">
          <circle cx="6" cy="6" r="5.5" fill="var(--blue-deep)"/>
          <ellipse cx="6" cy="6" rx="2.2" ry="5" stroke="var(--white)" stroke-width="0.8" fill="none"/>
          <line x1="1" y1="6" x2="11" y2="6" stroke="var(--white)" stroke-width="0.8"/>
        </svg>
      </li>
    </ul>
  </section>

</main>
</body>
</html>
```